Gooey Tides

I am creating an online slime shop that will sell handmade custom slimes. I need to be able to have payment/shipping options and the ability to change product photos since the product and product name will change often

Target Market(s)

Slime

Industry/Entity Type

Retail - online sales

Coding

Coded - Design and coding required

Number of Pages Required

2 page

Font styles to use
Sans Serif

Colors
0094D4
00A9DD
6FCCEA
C7EBF8
E9F6FB
E54698
E96AAD
F1A4CE
F9D9EA
FCEFF6
A7469A
B969AE
D3A5CF
EDDBEB
F8F0F9

Requirements
Must have
• My logo, my domain, ability to change photos of products for sale, payment options, shipping options, social media links, contact us,

```html
<!DOCTYPE html>
<html lang="en">
<head>
<meta charset="utf-8">
<title>Gooey Tides — Handmade Slime Shop</title>
<link href="https://fonts.googleapis.com/css2?family=Montserrat:wght@400;500;600;700&display=swap" rel="stylesheet">
<style>
:root{
  --ink:#1b1b1b;
  --dark:#3a3a3a;
  --footer:#353535;
  --purple:#8a3fc7;
  --purple-deep:#7a2fbd;
  --pink-soft:#f1d6ea;
  --lavender:#f1ebf4;
  --card-cyan:#eef9fb;
  --card-pink:#f9e9f3;
  --white:#ffffff;
  --muted:#444;
  --line:#bdbdbd;
}
*{margin:0;padding:0;box-sizing:border-box}
html,body{width:1200px;height:4501px;overflow:hidden;background:var(--white)}
body{font-family:"Montserrat",sans-serif;color:var(--ink)}
.page{position:relative;width:1200px;height:4501px;overflow:hidden}
.abs{position:absolute}
.center{left:0;width:1200px;text-align:center}
.btn{position:absolute;display:flex;align-items:center;justify-content:center;border-radius:24px;font-weight:700;font-size:14px;letter-spacing:.3px;text-transform:uppercase}
.btn-purple{background:var(--purple);color:var(--white)}
.placeholder{position:absolute}
.body-text{font-size:14px;line-height:28px;color:var(--muted)}
.section-title{font-weight:700;font-size:36px;letter-spacing:.3px;color:var(--ink)}

/* top bar */
.topbar{top:0;left:0;width:1200px;height:42px;background:#111;color:#fff;font-size:12px;font-weight:500;display:flex;align-items:center;justify-content:center}

/* hero */
.hero{top:42px;left:0;width:1200px;height:599px;background:linear-gradient(180deg,#e9d8ea 0%,#c98a8e 28%,#e38c3c 52%,#b35bc0 72%,#7b3f99 100%)}
.hero-shade{top:42px;left:0;width:1200px;height:599px;background:rgba(40,20,40,.18)}
.logo{display:flex;align-items:center;gap:8px;font-weight:700;font-size:20px;color:var(--purple-deep)}
.logo-dot{width:22px;height:22px;border-radius:50%;background:var(--ink)}
.nav{top:137px;left:0;width:1200px;display:flex;justify-content:center;gap:44px;font-size:13px;font-weight:500;color:var(--ink)}
.nav .active{font-weight:700;text-decoration:underline;text-underline-offset:4px}
.hero-kicker{top:224px;font-size:26px;font-weight:600;letter-spacing:2px;color:#fff}
.hero-title{top:262px;font-size:60px;font-weight:700;letter-spacing:3px;color:#fff}
.hero-text{top:340px;left:295px;width:610px;text-align:center;font-size:17px;line-height:27px;color:#fff}
.btn-white{background:#fff;color:var(--purple-deep)}

/* about */
.about-title{top:758px;left:131px}
.about-text{top:824px;left:131px;width:430px}

/* featured */
.featured-bg{top:1249px;left:0;width:1200px;height:791px;background:linear-gradient(135deg,#efe6f1,#f6f1f7 45%,#ece3ef)}
.product-card{position:absolute;top:1509px;width:297px;height:411px;background:var(--card-cyan)}
.product-card .img{position:absolute;left:30px;top:20px;width:237px;height:200px;border-radius:50%}
.product-card h3{position:absolute;top:244px;width:100%;text-align:center;font-size:19px;font-weight:600}
.product-card p{position:absolute;top:282px;left:30px;width:237px;text-align:center;font-size:13.5px;line-height:28px;color:var(--muted)}
.product-card .btn{top:349px;left:77px;width:142px;height:36px;font-size:12px}
.arrow{position:absolute;width:54px;height:54px}

/* new arrivals */
.arrivals-bg{top:2040px;left:0;width:1200px;height:486px;background:var(--dark)}
.arrivals-title{top:2122px;left:624px;color:#fff}
.arrivals-text{top:2190px;left:624px;width:440px;color:#e8e8e8}
.btn-soft{background:var(--pink-soft);color:var(--dark)}

/* best seller */
.best-card{position:absolute;top:2789px;width:233px}
.best-card .frame{position:relative;height:235px;background:var(--card-pink)}
.best-card .frame .img{position:absolute;left:20px;top:38px;width:160px;height:160px;border-radius:50%}
.best-card .tag{position:absolute;right:10px;top:50%;transform:translateY(-50%) rotate(-90deg);font-size:16px;color:var(--ink);white-space:nowrap}
.best-card h3{margin:18px 0 0 14px;font-size:19px;font-weight:600}
.best-card p{margin:4px 0 0 16px;font-size:13.5px;line-height:24px;color:var(--muted);width:210px}

/* gallery */
.gallery-band{top:3298px;left:0;width:1200px;height:367px;background:linear-gradient(135deg,#efe6f1,#f7f2f8)}

/* footer */
.footer{top:4085px;left:0;width:1200px;height:416px;background:var(--footer);color:#fff}
.foot-head{position:absolute;font-size:19px;font-weight:600;letter-spacing:.3px;color:#fff}
.foot-links{position:absolute;list-style:none;font-size:14px;line-height:27.5px;color:#fff}
.pay{position:absolute;top:4313px;width:40px;height:25px;border-radius:3px;background:#fff}
.social{position:absolute;top:4435px;width:34px;height:34px;border-radius:50%;background:#fff}
</style>
</head>
<body>
<div class="page">

  <div class="abs topbar">Free Shipping On Order Over $79 &nbsp;|&nbsp; lorem Ipsum- Get $15 OFF $99+ Code "lorem"</div>

  <!-- hero -->
  <div class="abs hero" role="img" aria-label="Close-up of cups filled with colourful orange, purple and green slime"></div>
  <div class="abs hero-shade"></div>
  <div class="abs center" style="top:72px;display:flex;justify-content:center">
    <div class="logo"><span class="logo-dot"></span>Gooey Tides</div>
  </div>
  <svg class="abs" style="top:72px;left:978px" width="100" height="30" viewBox="0 0 100 30" aria-label="Search, account and cart">
    <g fill="none" stroke="#111" stroke-width="2">
      <circle cx="12" cy="13" r="7"/><line x1="17" y1="18" x2="23" y2="24"/>
      <circle cx="53" cy="10" r="5"/><path d="M44 24c1-6 5-8 9-8s8 2 9 8"/>
      <path d="M85 10h12l-1 14H86z"/><path d="M88 10c0-5 6-5 6 0"/>
    </g>
    <circle cx="97" cy="5" r="5" fill="#00A9DD"/>
  </svg>
  <nav class="abs nav">
    <span class="active">HOME</span><span>PRODUCTS</span><span>BLOG</span><span>SHOP</span><span>REVIEWS</span><span>CONTACT US</span>
  </nav>
  <div class="abs center hero-kicker">WELCOME TO</div>
  <div class="abs center hero-title">GOOEY TIDES</div>
  <p class="abs hero-text">Lorem Ipsum is simply dummy text of the printing and typesetting industry. Lorem Ipsum has been the industry's standard dummy text ever since the 1500s,</p>
  <div class="btn btn-white" style="top:444px;left:522px;width:154px;height:45px">Shop Now</div>

  <!-- about -->
  <h2 class="abs section-title about-title">ABOUT US</h2>
  <p class="abs body-text about-text">Lorem Ipsum is simply dummy text of the printing and typesetting industry. Lorem Ipsum has been the industry's standard dummy text ever since the 1500s, when an unknown printer took a galley of type and scrambled it to make a type specimen book. It has survived not only five centuries, but also the leap into electronic typesetting, remaining essentially unchanged.</p>
  <div class="btn btn-purple" style="top:1080px;left:127px;width:154px;height:47px">Read More</div>
  <div class="placeholder" style="top:742px;left:624px;width:216px;height:144px;background:linear-gradient(135deg,#e9eef0,#e6b8d6)" role="img" aria-label="Girl playing with pink slime at a table"></div>
  <div class="placeholder" style="top:896px;left:624px;width:216px;height:248px;background:linear-gradient(160deg,#d9d2cc,#6fcdea 55%,#c9bfb6)" role="img" aria-label="Hands stretching blue slime"></div>
  <div class="placeholder" style="top:795px;left:851px;width:216px;height:318px;background:linear-gradient(135deg,#3fa9e0,#f2d23a 40%,#e54698 70%,#a7469a)" role="img" aria-label="Hand covered in rainbow coloured slime"></div>
  <div class="placeholder" style="top:1114px;left:1085px;width:103px;height:135px;background:linear-gradient(180deg,#f2f2f2,#d6d6d6);border-radius:40px 40px 6px 6px" role="img" aria-label="Panda mascot illustration"></div>

  <!-- featured -->
  <div class="abs featured-bg"></div>
  <h2 class="abs center section-title" style="top:1326px">FEATURED PRODUCTS</h2>
  <p class="abs body-text" style="top:1394px;left:190px;width:820px;text-align:center">Lorem Ipsum is simply dummy text of the printing and typesetting industry. Lorem Ipsum has been the industry's standard dummy text ever since the 1500s, when an unknown printer took a galley of type and scrambled it to make a type specimen book.</p>

  <div class="product-card" style="left:110px">
    <div class="img" style="background:radial-gradient(circle,#c07ee0,#a7469a 55%,transparent 72%)" role="img" aria-label="Purple glitter slime splash"></div>
    <h3>Lorem Ipsum</h3><p>Lorem Ipsum is simply dummy text of the printing and</p>
    <div class="btn btn-purple">View Product</div>
  </div>
  <div class="product-card" style="left:451px">
    <div class="img" style="background:radial-gradient(circle,#b7e27a,#7cc53e 55%,transparent 72%)" role="img" aria-label="Green jelly slime swirl"></div>
    <h3>Lorem Ipsum</h3><p>Lorem Ipsum is simply dummy text of the printing and</p>
    <div class="btn btn-purple">View Product</div>
  </div>
  <div class="product-card" style="left:790px">
    <div class="img" style="background:radial-gradient(circle,#c9487a,#8c1f4f 55%,transparent 72%)" role="img" aria-label="Red glitter slime blob"></div>
    <h3>Lorem Ipsum</h3><p>Lorem Ipsum is simply dummy text of the printing and</p>
    <div class="btn btn-purple">View Product</div>
  </div>

  <svg class="arrow" style="top:1692px;left:18px" viewBox="0 0 54 54" aria-label="Previous"><circle cx="27" cy="27" r="25" fill="none" stroke="#555" stroke-width="2"/><path d="M38 27H16M24 19l-8 8 8 8" fill="none" stroke="#555" stroke-width="2.5"/></svg>
  <svg class="arrow" style="top:1692px;left:1124px" viewBox="0 0 54 54" aria-label="Next"><circle cx="27" cy="27" r="25" fill="none" stroke="#8a3fc7" stroke-width="2"/><path d="M16 27h22M30 19l8 8-8 8" fill="none" stroke="#8a3fc7" stroke-width="2.5"/></svg>

  <!-- new arrivals -->
  <div class="abs arrivals-bg"></div>
  <div class="placeholder" style="top:2052px;left:44px;width:559px;height:474px;background:linear-gradient(120deg,#5a4a78,#8e7fb5 35%,#e0d05a 60%,#d8467e 85%,#3a3a3a)" role="img" aria-label="Two children stretching green and yellow slime"></div>
  <h2 class="abs section-title arrivals-title">NEW ARRIVALS</h2>
  <p class="abs body-text arrivals-text">Lorem Ipsum is simply dummy text of the printing and typesetting industry. Lorem Ipsum has been the industry's standard dummy text ever since the 1500s, when an unknown printer took a galley of type and scrambled it to make a type specimen book. It has survived not only five centuries, but also the leap into</p>
  <div class="btn btn-soft" style="top:2388px;left:618px;width:154px;height:47px">Read More</div>

  <!-- best seller -->
  <h2 class="abs center section-title" style="top:2603px">BEST SELLER</h2>
  <p class="abs body-text" style="top:2667px;left:190px;width:820px;text-align:center">Lorem Ipsum is simply dummy text of the printing and typesetting industry. Lorem Ipsum has been the industry's standard dummy text ever since the 1500s, when an unknown printer took a galley of type and scrambled it to make a type specimen book.</p>

  <div class="best-card" style="left:113px">
    <div class="frame"><div class="img" style="background:radial-gradient(circle,#c07ee0,#a7469a 55%,transparent 72%)" role="img" aria-label="Purple slime splash"></div><span class="tag">Purple slime</span></div>
    <h3>Lorem Ipsum</h3><p>Lorem Ipsum is simply dummy text of the printing</p>
  </div>
  <div class="best-card" style="left:362px">
    <div class="frame"><div class="img" style="background:radial-gradient(circle,#6fccea,#0094D4 55%,transparent 72%)" role="img" aria-label="Blue slime splash"></div><span class="tag">Blue slime</span></div>
    <h3>Lorem Ipsum</h3><p>Lorem Ipsum is simply dummy text of the printing</p>
  </div>
  <div class="best-card" style="left:611px">
    <div class="frame"><div class="img" style="background:radial-gradient(circle,#f06a86,#e23a5c 55%,transparent 72%)" role="img" aria-label="Red slime splash"></div><span class="tag">Red slime</span></div>
    <h3>Lorem Ipsum</h3><p>Lorem Ipsum is simply dummy text of the printing</p>
  </div>
  <div class="best-card" style="left:859px">
    <div class="frame"><div class="img" style="background:radial-gradient(circle,#f8d84a,#f0b400 55%,transparent 72%)" role="img" aria-label="Yellow slime splash"></div><span class="tag">Yellow slime</span></div>
    <h3>Lorem Ipsum</h3><p>Lorem Ipsum is simply dummy text of the printing</p>
  </div>

  <svg class="arrow" style="top:2934px;left:18px" viewBox="0 0 54 54" aria-label="Previous"><circle cx="27" cy="27" r="25" fill="none" stroke="#555" stroke-width="2"/><path d="M38 27H16M24 19l-8 8 8 8" fill="none" stroke="#555" stroke-width="2.5"/></svg>
  <svg class="arrow" style="top:2934px;left:1124px" viewBox="0 0 54 54" aria-label="Next"><circle cx="27" cy="27" r="25" fill="none" stroke="#8a3fc7" stroke-width="2"/><path d="M16 27h22M30 19l8 8-8 8" fill="none" stroke="#8a3fc7" stroke-width="2.5"/></svg>

  <div class="placeholder" style="top:3144px;left:0;width:157px;height:154px;background:linear-gradient(180deg,#f0f0f0,#cfcfcf);border-radius:0 70px 0 0" role="img" aria-label="Panda mascot illustration"></div>
  <div class="btn btn-purple" style="top:3179px;left:520px;width:154px;height:46px">Shop Now</div>

  <!-- gallery -->
  <div class="abs gallery-band"></div>
  <h2 class="abs center section-title" style="top:3370px">OUR GALLERY</h2>
  <div class="placeholder" style="top:3445px;left:110px;width:309px;height:459px;background:linear-gradient(160deg,#d2465f,#c89bd2 60%,#cf4563)" role="img" aria-label="Smiling girl stretching red slime"></div>
  <div class="placeholder" style="top:3445px;left:447px;width:309px;height:220px;background:linear-gradient(90deg,#1eb3d6,#e8a060 45%,#7a4fa8 60%,#1eb3d6)" role="img" aria-label="Hands pulling rainbow slime on blue background"></div>
  <div class="placeholder" style="top:3684px;left:447px;width:309px;height:220px;background:linear-gradient(135deg,#f5e77a,#7fd7c8 45%,#9fdc8a 60%,#e79acb)" role="img" aria-label="Containers of yellow, green and pink slime"></div>
  <div class="placeholder" style="top:3445px;left:784px;width:309px;height:459px;background:linear-gradient(170deg,#1c3a66,#3fa0d8 45%,#1d5d9e 80%,#27466e)" role="img" aria-label="Hands kneading blue slime in a bowl"></div>
  <div class="btn btn-purple" style="top:3958px;left:520px;width:154px;height:45px">View More</div>

  <!-- footer -->
  <div class="abs footer"></div>
  <div class="abs" style="top:4205px;left:122px">
    <div class="logo" style="color:#fff"><span class="logo-dot" style="background:#fff"></span>Gooey Tides</div>
  </div>
  <div class="pay" style="left:133px"></div>
  <div class="pay" style="left:184px"></div>
  <div class="pay" style="left:235px"></div>
  <div class="pay" style="left:286px"></div>

  <div class="foot-head" style="top:4163px;left:391px">MAIN LINKS</div>
  <ul class="foot-links" style="top:4214px;left:392px">
    <li>Home</li><li>Products</li><li>Blog</li><li>Shop</li><li>Reviews</li><li>Contact Us</li>
  </ul>
  <div class="foot-head" style="top:4163px;left:608px">OTHER LINKS</div>
  <ul class="foot-links" style="top:4214px;left:611px">
    <li>Careers</li><li>Privacy Policy</li><li>Terms &amp; Conditions</li>
  </ul>
  <div class="foot-head" style="top:4163px;left:873px;line-height:28px">SIGN UP TO OUR<br>NEWSLETTER</div>
  <p class="abs" style="top:4233px;left:872px;width:200px;font-size:12px;line-height:26px;color:#fff">We Will Notify You Of Any Important News</p>
  <div class="abs" style="top:4295px;left:872px;width:216px;height:44px;background:#fff;border-radius:4px;display:flex;align-items:center;padding-left:10px;font-size:12px;color:#666">Your Email Address</div>
  <svg class="abs" style="top:4298px;left:1042px" width="42" height="38" viewBox="0 0 42 38" aria-label="Subscribe">
    <rect width="42" height="38" rx="4" fill="#8a3fc7"/>
    <path d="M11 19l21-9-7 20-4-8z M21 22l11-12" fill="none" stroke="#fff" stroke-width="2" stroke-linejoin="round"/>
  </svg>

  <div class="abs" style="top:4416px;left:115px;width:973px;height:2px;background:var(--line)"></div>
  <div class="social" style="left:123px"></div>
  <div class="social" style="left:180px"></div>
  <div class="social" style="left:236px"></div>
  <div class="abs" style="top:4447px;left:700px;width:385px;text-align:right;font-size:13px;color:#fff">© 2024 Gooey Tides | All Rights Reserved</div>

</div>
</body>
</html>
```